Dalvick's Business Card

I need some designs for a new business card including the new logo attached. An old example of our business card is also attached to show all the data that should be included on the new design.
**I added some more examples someone had mocked up**

Contact Information for Business Card

Should include all info on other examples uploaded.

```html
<!DOCTYPE html>
<html lang="en">
<head>
<meta charset="UTF-8">
<title>Dalvick's Business Card</title>
<link href="https://fonts.googleapis.com/css2?family=Montserrat:wght@400;700;800&family=Oswald:wght@500&display=swap" rel="stylesheet">
<style>
  :root {
    --stage: #1c1c1c;
    --card-black: #141414;
    --card-white: #ffffff;
    --brand-red: #ec1c24;
    --brand-blue: #0b72c0;
    --text-white: #ffffff;
  }
  * { margin: 0; padding: 0; box-sizing: border-box; }
  html, body { width: 1200px; height: 1015px; overflow: hidden; }
  body {
    background: var(--stage);
    font-family: "Montserrat", Arial, sans-serif;
    position: relative;
  }
  .card {
    position: absolute;
    left: 250px;
    width: 700px;
    height: 400px;
    overflow: hidden;
  }
  .card-back { top: 50px; background: var(--card-black); }
  .card-front { top: 520px; background: var(--card-white); }

  /* back */
  .brand-lockup {
    position: absolute;
    top: 110px;
    left: 0; right: 0;
    display: flex;
    align-items: center;
    justify-content: center;
    gap: 22px;
  }
  .brand-dot {
    width: 62px; height: 62px;
    border-radius: 50%;
    background: var(--brand-red);
  }
  .brand-name {
    color: var(--brand-blue);
    font-weight: 800;
    font-size: 72px;
    letter-spacing: 2px;
    text-transform: uppercase;
    line-height: 1;
  }
  .band {
    position: absolute;
    left: 0; right: 0;
    display: flex;
    align-items: center;
    justify-content: center;
    padding: 0 32px;
    color: var(--text-white);
    white-space: nowrap;
  }
  .band-area {
    top: 272px; height: 60px;
    background: var(--brand-red);
    font-weight: 700;
    font-size: 26px;
  }
  .band-call {
    top: 332px; height: 68px;
    background: var(--brand-blue);
    font-family: "Oswald", "Arial Narrow", sans-serif;
    font-weight: 500;
    font-size: 23px;
    letter-spacing: -0.3px;
  }

  /* front */
  .contact {
    position: absolute;
    left: 56px;
    top: 92px;
    width: 380px;
  }
  .person-name {
    color: var(--brand-red);
    font-weight: 700;
    font-size: 34px;
    text-transform: uppercase;
    letter-spacing: 0.5px;
  }
  .rule {
    width: 120px;
    height: 2px;
    background: var(--brand-blue);
    margin: 12px 0 16px;
  }
  .contact-line {
    display: flex;
    align-items: center;
    gap: 12px;
    color: var(--brand-blue);
    font-size: 22px;
    line-height: 1.35;
    white-space: nowrap;
  }
  .contact-line svg { width: 22px; height: 22px; flex: none; }
  .rule-lower { margin-top: 18px; }
  .claim {
    font-weight: 800;
    font-size: 22px;
    text-transform: uppercase;
    letter-spacing: 0.5px;
    line-height: 1.45;
    white-space: nowrap;
  }
  .claim-licensed { color: var(--brand-blue); }
  .claim-family { color: var(--brand-red); }

  .front-brand {
    position: absolute;
    right: 40px;
    top: 100px;
    width: 220px;
    display: flex;
    flex-direction: column;
    align-items: center;
    gap: 18px;
  }
  .front-brand .brand-dot { width: 120px; height: 120px; }
  .front-brand .brand-name { font-size: 38px; }
</style>
</head>
<body>
  <section class="card card-back">
    <div class="brand-lockup">
      <span class="brand-dot"></span>
      <span class="brand-name">Dalvick's</span>
    </div>
    <div class="band band-area">Serves Millbrook, IA &amp; Surrounding Areas</div>
    <div class="band band-call">CALL TODAY FOR ALL YOUR HVAC, REFRIGERATION &amp; PLUMBING NEEDS</div>
  </section>

  <section class="card card-front">
    <div class="contact">
      <h1 class="person-name">Steve Dalvick</h1>
      <div class="rule"></div>
      <p class="contact-line">
        <svg viewBox="0 0 24 24" aria-hidden="true"><path fill="var(--brand-red)" d="M6.6 10.8a15 15 0 0 0 6.6 6.6l2.2-2.2a1 1 0 0 1 1-.25 11.4 11.4 0 0 0 3.6.57 1 1 0 0 1 1 1V20a1 1 0 0 1-1 1A17 17 0 0 1 3 4a1 1 0 0 1 1-1h3.5a1 1 0 0 1 1 1c0 1.25.2 2.45.57 3.57a1 1 0 0 1-.25 1z"/></svg>
        555.014.2290
      </p>
      <p class="contact-line">
        <svg viewBox="0 0 24 24" aria-hidden="true"><path fill="var(--brand-red)" d="M2 5h20v14H2z"/><path fill="none" stroke="#fff" stroke-width="1.6" d="M2.5 5.5 12 13l9.5-7.5"/></svg>
        hvacdalvick@mailbox.com
      </p>
      <div class="rule rule-lower"></div>
      <p class="claim claim-licensed">Licensed &amp; Insured</p>
      <p class="claim claim-family">Family Owned &amp; Operated</p>
    </div>
    <div class="front-brand">
      <span class="brand-dot"></span>
      <span class="brand-name">Dalvick's</span>
    </div>
  </section>
</body>
</html>
```